redesign of my existing custom website into Wordpress based website

I need someone to redesign my current website into something more classy, simplistic, modern and on trend. I would like it set up on Wordpress in a way thats easy for me to make my own additions to blogs/price changes and promotion banners. I will also need a page that is password protected so members can login and have access to all my training videos and resources.
website is www.tidewellmamas.com.au

Target Market(s)

new mums

Industry/Entity Type

Fitness

Coding

Coded - Design and coding required

Number of Pages Required

5+ page

Colors
33a6d7

Requirements
Must have
• chic, modern, stylish and simplistic.
• a call to action above the page fold
• mobile friendly conversion
• a pop up message as soon as someone enters my sight offering my free report
• a members page that is password protected containing 3 youtube videos and 6 pdf attachments as resources
• a home page
• a contact us page
• an about us page
• a blog page
• a store page
Nice to have
• some examples of my peers websites that I like:
• www.norapellwick.com
• https://www.9qlr.com
• https://41bytedgarth.com
Should not have
• anything gimmicky

```html
<!DOCTYPE html>
<html lang="en">
<head>
<meta charset="utf-8">
<title>Tidewell Mamas — Home Fitness for New Mums</title>
<link href="https://fonts.googleapis.com/css2?family=Titillium+Web:wght@300;400;600;700&family=Great+Vibes&display=swap" rel="stylesheet">
<style>
:root{
  --blue:#33a6d7;
  --blue-dark:#2a93c2;
  --pink:#e5177e;
  --ink:#333a40;
  --muted:#8a9095;
  --line:#e3e6e8;
  --soft:#f3f4f5;
  --white:#ffffff;
  --dark:#1d1f22;
}
*{box-sizing:border-box;margin:0;padding:0}
html,body{width:1200px;height:3846px;overflow:hidden}
body{font-family:"Titillium Web",Arial,sans-serif;color:var(--ink);background:var(--white);position:relative}
a{color:inherit;text-decoration:none}
ul{list-style:none}
.btn{display:inline-flex;align-items:center;justify-content:center;background:var(--blue);color:var(--white);font-weight:600;font-size:15px;border-radius:3px}
.section{position:absolute;left:0;width:1200px}

/* header */
.topline{position:absolute;top:0;left:400px;right:0;height:3px;background:var(--blue)}
.site-header{position:absolute;top:0;left:0;width:1200px;height:128px;z-index:5}
.brand{position:absolute;left:128px;top:20px;width:165px;height:165px;border-radius:50%;border:4px solid #222;background:var(--white);display:flex;align-items:center;justify-content:center;text-align:center;color:var(--pink);font-size:19px;font-weight:600;line-height:1.15}
.main-nav{position:absolute;left:402px;top:48px;display:flex;align-items:center;font-size:14px}
.main-nav a{padding:0 21px;height:38px;display:flex;align-items:center}
.main-nav a.active{background:var(--blue);color:var(--white);border-radius:3px;width:83px;justify-content:center;padding:0;margin-right:4px}
.cart{position:absolute;left:949px;top:52px;display:flex;align-items:center;gap:9px;font-size:13px}
.cart .dot{width:30px;height:30px;border-radius:50%;background:var(--blue);display:flex;align-items:center;justify-content:center}
.cart b{color:var(--blue);font-weight:600}

/* hero */
.hero{top:0;height:662px;background:var(--white)}
.hero-photo{position:absolute;left:487px;top:128px;width:713px;height:534px;background:linear-gradient(90deg,#fff 0%,#f1ece6 22%,#e6ddd3 55%,#cfc6c4 80%,#b9b1c9 100%)}
.hero-copy{position:absolute;left:110px;top:240px;width:450px;text-align:center}
.hero-title{font-family:"Great Vibes",cursive;color:var(--pink);font-size:70px;font-weight:400;line-height:1;white-space:nowrap;margin-left:18px;text-align:left}
.hero-sub{font-size:30px;font-weight:400;line-height:1.4;margin-top:18px}
.hero-price{font-size:16px;margin-top:20px}
.hero-price b{color:var(--blue);font-size:32px;font-weight:700;vertical-align:-3px}
.hero .btn{width:213px;height:44px;margin-top:24px;font-size:14px}
.hero-rule{position:absolute;left:487px;right:0;top:658px;height:4px;background:var(--blue)}

/* video */
.intro{top:667px;height:359px;background:var(--white)}
.video{position:absolute;left:0;top:0;width:597px;height:359px;background:linear-gradient(135deg,#3b3a3c,#6a5f63 45%,#2e2c2e)}
.video-bar{position:absolute;left:0;right:0;bottom:0;height:36px;background:rgba(0,0,0,.55);display:flex;align-items:center;gap:14px;padding:0 14px}
.video-bar .track{flex:1;height:4px;background:rgba(255,255,255,.3);position:relative}
.video-bar .track i{position:absolute;left:0;top:0;height:4px;width:28%;background:var(--blue)}
.video-bar span{color:#fff;font-size:11px;font-weight:600}
.intro-copy{position:absolute;left:656px;top:52px;width:480px}
.intro-copy h2{font-size:21px;font-weight:400;line-height:1.45}
.ticks{margin-top:22px}
.ticks li{display:flex;align-items:center;gap:14px;font-size:13px;height:29px}
.intro-copy .btn{width:139px;height:42px;margin-top:20px;font-size:14px}

/* optin */
.optin{top:1026px;height:582px;background:linear-gradient(180deg,#cfcfd1,#e2e2e3 45%,#bdbcbd)}
.optin-bg{position:absolute;inset:0;background:linear-gradient(135deg,rgba(120,110,110,.35),rgba(255,255,255,.25) 50%,rgba(90,90,95,.35))}
.optin-box{position:absolute;left:274px;top:128px;width:654px;height:333px;background:var(--white);box-shadow:0 0 0 6px rgba(255,255,255,.5),0 4px 14px rgba(0,0,0,.18)}
.optin-photo{position:absolute;left:20px;top:18px;width:190px;height:300px;background:linear-gradient(180deg,#d8dcd5,#9fd36a 40%,#3a3b3d 75%,#2b2b2d)}
.optin-copy{position:absolute;left:234px;top:30px;width:390px}
.optin-copy h3{font-size:23px;font-weight:400;line-height:1.3;width:330px}
.optin-copy h3 em{font-style:normal;color:var(--pink)}
.optin-copy p{font-size:13px;line-height:1.5;margin-top:12px;color:#555;width:340px}
.field{width:384px;height:36px;border:1px solid var(--line);border-radius:2px;font-size:11px;color:#888;display:flex;align-items:center;padding:0 10px;margin-top:10px}
.field:first-of-type{margin-top:16px}
.optin-copy .btn{width:141px;height:46px;margin-top:16px;font-size:14px}
.free-badge{position:absolute;left:556px;top:-77px;width:106px;height:106px;border-radius:50%;background:var(--blue);color:#fff;display:flex;align-items:center;justify-content:center;text-align:center;font-size:14px;line-height:1.3}

/* results */
.results{top:1608px;height:648px;background:var(--white)}
.results h2{position:absolute;top:62px;width:100%;text-align:center;font-size:24px;font-weight:400;line-height:1.6;color:#3c4247}
.result-card{position:absolute;top:169px;width:297px;height:397px;border:1px solid var(--line);background:#fff}
.pair{display:flex;gap:6px;height:210px}
.pair div{flex:1}
.before{background:linear-gradient(180deg,#f4f4f4,#e9dcd2 45%,#4a5160 85%)}
.after{background:linear-gradient(180deg,#f4f4f4,#ecdccf 45%,#49526a 85%)}
.lost{position:absolute;left:189px;top:172px;width:76px;height:76px;border-radius:50%;background:var(--pink);color:#fff;text-align:center;display:flex;flex-direction:column;justify-content:center;font-size:11px;font-weight:600;line-height:1.1}
.lost b{font-size:22px;font-weight:600}
.result-card h4{font-size:15px;font-weight:400;margin:38px 0 0 22px}
.result-card p{font-size:11.5px;line-height:1.55;color:var(--muted);margin:6px 20px 0 22px}
.more{display:flex;align-items:center;gap:8px;font-size:11.5px;color:var(--blue);margin:14px 0 0 22px}

/* equipment */
.equip{top:2256px;height:359px}
.equip-panel{position:absolute;left:0;top:0;width:597px;height:359px;background:var(--blue);color:#fff;padding:45px 0 0 131px}
.equip-panel h2{font-size:24px;font-weight:400;line-height:1.45}
.equip-list{margin-top:22px}
.equip-list li{display:flex;align-items:center;gap:14px;font-size:13.5px;height:40px}
.equip-photo{position:absolute;left:597px;top:0;width:603px;height:359px;background:linear-gradient(135deg,#3a3233,#5b4f4c 40%,#6d5a74 75%,#2d2628)}

/* news */
.news{top:2615px;height:572px;background:var(--soft)}
.news h2{position:absolute;top:72px;width:100%;text-align:center;font-size:27px;font-weight:400}
.news-card{position:absolute;top:144px;width:218px;height:346px;background:#fff;border:1px solid var(--line);text-align:center}
.news-img{height:164px}
.news-card h4{font-size:14px;font-weight:400;line-height:1.4;margin:22px 12px 0}
.news-card p{font-size:10.5px;line-height:1.5;color:var(--muted);margin:10px 24px 0}
.news-meta{position:absolute;left:0;right:0;bottom:26px;display:flex;justify-content:center;align-items:center;gap:18px;font-size:12px}
.news-meta b{color:var(--blue);font-weight:600;font-size:14px}
.news-meta span{display:flex;align-items:center;gap:5px;color:var(--muted)}

/* cta */
.cta{top:3187px;height:287px;background:linear-gradient(135deg,#141414,#2b2a2a 45%,#171717);text-align:center;color:#fff}
.cta h2{padding-top:66px;font-size:32px;font-weight:700;color:var(--blue);line-height:1.2}
.cta p{font-size:18px;margin-top:4px}
.cta .btn{width:139px;height:48px;margin-top:18px;font-size:14px}

/* footer */
.site-footer{top:3474px;height:372px;background:#fff}
.f-col{position:absolute;top:48px}
.f-col h5{font-size:15px;font-weight:400;margin-bottom:12px}
.f-col li{font-size:12px;height:27px;color:#555}
.fb-box{position:absolute;left:597px;top:39px;width:239px;height:190px;border:1px solid #d5d8dd;background:#fff;font-size:10px;color:#444;padding:6px 8px}
.fb-head{font-weight:600;border-bottom:1px solid #e3e3e3;padding-bottom:5px}
.fb-page{display:flex;gap:8px;align-items:center;margin-top:8px}
.fb-page i{width:40px;height:40px;border:1px solid #ddd;background:#fbeef4;display:block}
.fb-like{display:inline-block;background:#4a67a8;color:#fff;font-size:9px;padding:2px 6px;border-radius:2px;margin-top:3px}
.fb-grid{display:grid;grid-template-columns:repeat(5,34px);gap:5px;margin-top:8px}
.fb-grid i{height:34px;background:linear-gradient(135deg,#c9b6c8,#6b7fa6);display:block}
.social li{display:flex;align-items:center;gap:10px;height:33px}
.social .ic{width:24px;height:24px;border-radius:50%;display:block}
.copyright{position:absolute;left:131px;right:131px;top:302px;border-top:1px solid var(--line);padding-top:16px;text-align:center;font-size:11px;color:#555}
</style>
</head>
<body>

<div class="topline"></div>

<header class="site-header">
  <a class="brand" href="#">Tidewell<br>Mamas</a>
  <nav class="main-nav">
    <a class="active" href="#">Home</a>
    <a href="#">About Us</a>
    <a href="#">Program</a>
    <a href="#">Blog</a>
    <a href="#">Shop</a>
    <a href="#">Contact</a>
  </nav>
  <div class="cart">
    <span class="dot"><svg width="15" height="13" viewBox="0 0 15 13"><path d="M0 1h3l2 7h7l2-5H4" fill="none" stroke="#fff" stroke-width="1.6"/><circle cx="6" cy="11" r="1.3" fill="#fff"/><circle cx="11" cy="11" r="1.3" fill="#fff"/></svg></span>
    <span>My Cart : <b>$0.00</b></span>
  </div>
</header>

<section class="section hero">
  <div class="hero-photo" role="img" aria-label="Smiling mum kneeling on an exercise mat while her baby reaches for a small dumbbell"></div>
  <div class="hero-copy">
    <h1 class="hero-title">Tidewell Mamas</h1>
    <p class="hero-sub">Start seeing amazing results in<br>just a few weeks!</p>
    <p class="hero-price">Starting from only <b>$7.50</b> per week!</p>
    <a class="btn" href="#">Click View More Information</a>
  </div>
  <div class="hero-rule"></div>
</section>

<section class="section intro">
  <div class="video" role="img" aria-label="Video still of a mum doing push-ups in her lounge room beside her toddler">
    <div class="video-bar">
      <svg width="12" height="14" viewBox="0 0 12 14"><path d="M0 0l12 7-12 7z" fill="#fff"/></svg>
      <div class="track"><i></i></div>
      <span>HD</span>
    </div>
  </div>
  <div class="intro-copy">
    <h2>Lose your baby weight and get back into shape!<br>12 week Home Workout Program For Mums!</h2>
    <ul class="ticks">
      <li><svg width="14" height="14" viewBox="0 0 14 14"><circle cx="7" cy="7" r="7" fill="var(--blue)"/><path d="M4 7.2l2 2 4-4.2" fill="none" stroke="#fff" stroke-width="1.6"/></svg>12 week, cardio and resistance circuit training program</li>
      <li><svg width="14" height="14" viewBox="0 0 14 14"><circle cx="7" cy="7" r="7" fill="var(--blue)"/><path d="M4 7.2l2 2 4-4.2" fill="none" stroke="#fff" stroke-width="1.6"/></svg>Workout equipment delivered to your front door</li>
      <li><svg width="14" height="14" viewBox="0 0 14 14"><circle cx="7" cy="7" r="7" fill="var(--blue)"/><path d="M4 7.2l2 2 4-4.2" fill="none" stroke="#fff" stroke-width="1.6"/></svg>Weekly coaching emails</li>
      <li><svg width="14" height="14" viewBox="0 0 14 14"><circle cx="7" cy="7" r="7" fill="var(--blue)"/><path d="M4 7.2l2 2 4-4.2" fill="none" stroke="#fff" stroke-width="1.6"/></svg>Accountability charts &amp; program cards</li>
    </ul>
    <a class="btn" href="#">Get Started Now!</a>
  </div>
</section>

<section class="section optin">
  <div class="optin-bg" role="img" aria-label="Faded photo of a living room with a workout mat"></div>
  <div class="optin-box">
    <div class="optin-photo" role="img" aria-label="Trainer in a bright green vest standing with hands on hips"></div>
    <div class="optin-copy">
      <h3>Get your <em>FREE TOP 10</em> Baby Belly Blasting Tips</h3>
      <p>See our secret tips to a flatter yummy mummy tummy that you can start implementing</p>
      <div class="field">Name*</div>
      <div class="field">E-mail*</div>
      <a class="btn" href="#">Get It FREE Now!</a>
    </div>
    <div class="free-badge">For Free<br>Today!</div>
  </div>
</section>

<section class="section results">
  <h2>Check out some of the awesome results already achieved<br>by mums on our program</h2>

  <article class="result-card" style="left:131px">
    <div class="pair"><div class="before" role="img" aria-label="Before photo of a mum in workout wear"></div><div class="after" role="img" aria-label="After photo of the same mum, slimmer"></div></div>
    <div class="lost">LOST<b>12</b>KGS</div>
    <h4>Marisol</h4>
    <p>Spending a lot of time researching the best post pregnancy training methods, I created this program to help me get back...</p>
    <a class="more" href="#">Read More Information <svg width="12" height="8" viewBox="0 0 12 8"><path d="M0 4h10M7 1l3 3-3 3" fill="none" stroke="currentColor" stroke-width="1.4"/></svg></a>
  </article>

  <article class="result-card" style="left:451px">
    <div class="pair"><div class="before" role="img" aria-label="Before photo of a mum in workout wear"></div><div class="after" role="img" aria-label="After photo of the same mum, slimmer"></div></div>
    <div class="lost">LOST<b>20</b>KGS</div>
    <h4>Brynn</h4>
    <p>Spending a lot of time researching the best post pregnancy training methods, I created this program to help me get back...</p>
    <a class="more" href="#">Read More Information <svg width="12" height="8" viewBox="0 0 12 8"><path d="M0 4h10M7 1l3 3-3 3" fill="none" stroke="currentColor" stroke-width="1.4"/></svg></a>
  </article>

  <article class="result-card" style="left:772px">
    <div class="pair"><div class="before" role="img" aria-label="Before photo of a mum in workout wear"></div><div class="after" role="img" aria-label="After photo of the same mum, slimmer"></div></div>
    <div class="lost">LOST<b>22</b>KGS</div>
    <h4>Odette</h4>
    <p>Spending a lot of time researching the best post pregnancy training methods, I created this program to help me get back...</p>
    <a class="more" href="#">Read More Information <svg width="12" height="8" viewBox="0 0 12 8"><path d="M0 4h10M7 1l3 3-3 3" fill="none" stroke="currentColor" stroke-width="1.4"/></svg></a>
  </article>
</section>

<section class="section equip">
  <div class="equip-panel">
    <h2>12 week Home Workout Program<br>Equipment Pack</h2>
    <ul class="equip-list">
      <li><svg width="20" height="20" viewBox="0 0 20 20"><circle cx="10" cy="10" r="9" fill="none" stroke="#fff" stroke-width="1.4"/><path d="M8 6l4 4-4 4" fill="none" stroke="#fff" stroke-width="1.6"/></svg>Our unique 3 stage, 12 week training program</li>
      <li><svg width="20" height="20" viewBox="0 0 20 20"><circle cx="10" cy="10" r="9" fill="none" stroke="#fff" stroke-width="1.4"/><path d="M8 6l4 4-4 4" fill="none" stroke="#fff" stroke-width="1.6"/></svg>Full Instructional Workout DVD program cards for each program</li>
      <li><svg width="20" height="20" viewBox="0 0 20 20"><circle cx="10" cy="10" r="9" fill="none" stroke="#fff" stroke-width="1.4"/><path d="M8 6l4 4-4 4" fill="none" stroke="#fff" stroke-width="1.6"/></svg>Funky exercise equipment for your home</li>
      <li><svg width="20" height="20" viewBox="0 0 20 20"><circle cx="10" cy="10" r="9" fill="none" stroke="#fff" stroke-width="1.4"/><path d="M8 6l4 4-4 4" fill="none" stroke="#fff" stroke-width="1.6"/></svg>Full Instructional Workout DVD program cards for each program</li>
      <li><svg width="20" height="20" viewBox="0 0 20 20"><circle cx="10" cy="10" r="9" fill="none" stroke="#fff" stroke-width="1.4"/><path d="M8 6l4 4-4 4" fill="none" stroke="#fff" stroke-width="1.6"/></svg>Healthy Family Favourites recipe ebook</li>
    </ul>
  </div>
  <div class="equip-photo" role="img" aria-label="Trainer stretching on a purple mat in a lounge room with hand weights"></div>
</section>

<section class="section news">
  <h2>Top News</h2>

  <article class="news-card" style="left:131px">
    <div class="news-img" role="img" aria-label="Mum training in the morning with a resistance band" style="background:linear-gradient(135deg,#3b2f33,#7a4f86 50%,#2a2628)"></div>
    <h4>The benefits of training in<br>the morning</h4>
    <p>Cum sociis natoque penatibus et magnis dis parturient montes nascetur...</p>
    <div class="news-meta"><b>JAN 02</b><span><svg width="13" height="12" viewBox="0 0 13 12"><path d="M6.5 11.5L1.2 6.2A3 3 0 0 1 6.5 2a3 3 0 0 1 5.3 4.2z" fill="var(--blue)"/></svg>21</span></div>
  </article>

  <article class="news-card" style="left:369px">
    <div class="news-img" role="img" aria-label="Trainer doing a floor exercise in a lounge room" style="background:linear-gradient(135deg,#2a2526,#5b4447 50%,#1e1b1c)"></div>
    <h4>Marisol's 10 exercise lounge<br>room cardio workout</h4>
    <p>Cum sociis natoque penatibus et magnis dis parturient montes nascetur...</p>
    <div class="news-meta"><b>JAN 02</b><span><svg width="13" height="12" viewBox="0 0 13 12"><path d="M6.5 11.5L1.2 6.2A3 3 0 0 1 6.5 2a3 3 0 0 1 5.3 4.2z" fill="var(--blue)"/></svg>21</span></div>
  </article>

  <article class="news-card" style="left:610px">
    <div class="news-img" role="img" aria-label="Golden baked pies on a white plate" style="background:linear-gradient(135deg,#e9e6df,#d9b877 50%,#b98b45)"></div>
    <h4>Healthy Shepherds Pie<br>Recipe</h4>
    <p>Cum sociis natoque penatibus et magnis dis parturient montes nascetur...</p>
    <div class="news-meta"><b>JAN 02</b><span><svg width="13" height="12" viewBox="0 0 13 12"><path d="M6.5 11.5L1.2 6.2A3 3 0 0 1 6.5 2a3 3 0 0 1 5.3 4.2z" fill="var(--blue)"/></svg>21</span></div>
  </article>

  <article class="news-card" style="left:851px">
    <div class="news-img" role="img" aria-label="Orange baked slices on a dark wooden table" style="background:linear-gradient(135deg,#3d2c22,#b8612b 50%,#4a3226)"></div>
    <h4>Dairy, Gluten, Sugar, Guilt Free<br>Easter the morning</h4>
    <p>Cum sociis natoque penatibus et magnis dis parturient montes nascetur...</p>
    <div class="news-meta"><b>JAN 02</b><span><svg width="13" height="12" viewBox="0 0 13 12"><path d="M6.5 11.5L1.2 6.2A3 3 0 0 1 6.5 2a3 3 0 0 1 5.3 4.2z" fill="var(--blue)"/></svg>21</span></div>
  </article>
</section>

<section class="section cta" role="img" aria-label="Dark background photo of a lounge room workout space">
  <h2>Take the first step today by joining our program</h2>
  <p>and let us help you get back to the body that you deserve!</p>
  <a class="btn" href="#">Get It FREE Now!</a>
</section>

<footer class="section site-footer">
  <div class="f-col" style="left:131px">
    <h5>Quick links</h5>
    <ul><li>Home</li><li>About Us</li><li>Programs</li><li>Blog</li><li>Shop</li><li>Contact</li><li>Website Policies</li></ul>
  </div>
  <div class="f-col" style="left:346px">
    <h5>More Information</h5>
    <ul><li>Terms &amp; Conditions</li><li>Privacy policy</li><li>Disclaimer</li><li>Why our program</li><li>Basic Pack</li><li>Equipment Pack</li><li>Faq</li></ul>
  </div>
  <div class="fb-box">
    <div class="fb-head">Find us on Chatterleaf</div>
    <div class="fb-page"><i></i><div>Tidewell Mamas<br><span class="fb-like">Like</span></div></div>
    <div style="margin-top:6px">4,183 people like Tidewell Mamas.</div>
    <div class="fb-grid"><i></i><i></i><i></i><i></i><i></i><i></i><i></i><i></i><i></i><i></i></div>
  </div>
  <div class="f-col" style="left:967px">
    <h5>Follow Us</h5>
    <ul class="social">
      <li><span class="ic" style="background:#3b5998"></span>Chatterleaf</li>
      <li><span class="ic" style="background:#29a9e1"></span>Peeplet</li>
      <li><span class="ic" style="background:#dc4a38"></span>Circlepost</li>
      <li><span class="ic" style="background:#cb2027"></span>Pinboardly</li>
      <li><span class="ic" style="background:#0e76a8"></span>Workmesh</li>
    </ul>
  </div>
  <div class="copyright">Copyrights © tidewellmamas.com 2017 | Allrights Reserved.</div>
</footer>

</body>
</html>
```